Elegant Business Card for Technology Company

Client is a supplier of innovative industrial communications and automation equipment since 2002. This contest is to gather fresh ideas for a redesign of the existing business card. Client is looking for design that best communicates tagline "Industrial Networking and Computing Specialist".

Design submissions should look modern, clean, elegant and professional. It should not be cluttered. Use white as the primary colour. Orange and black as secondary colour. Refer to jpeg File 1 on the current design.

Fonts used by Client used include Arial Regular, Arial Black, Roboto Regular, Roboto Black and Lato.

The winning design will be sent for offset printing using super white 250gsm artcard paper (open for suggestions).

Target Market(s)

System Engineers, Project Managers, Purchasing Managers from companies providing engineering services for Smart Cities.

Industry/Entity Type

Information Technology

Contact Information for Business Card

Refer to PDF File 3 for Business Card Details. Priority of short contact information would be as follows Name > Job Title > Email > Mobile > Web > Tel > Fax > Business Address >UEN (UEN represents company registration number)

Font styles to use
Sans Serif

Colors
ffffff
f37122
000000
5c5c5c

Requirements
Must have
• Refer to AI File 2 (Company Logo) & PDF File 3 (Information on Namecard)
Should not have
• No QR codes
• No Social Media Icons
• Do not create full Black or Orange colour background

```html
<!DOCTYPE html>
<html lang="en">
<head>
<meta charset="utf-8">
<title>Kestrel Asia Pacific – Business Card</title>
<link href="https://fonts.googleapis.com/css2?family=Lato:wght@400;700;900&display=swap" rel="stylesheet">
<style>
  :root {
    --white: #ffffff;
    --orange: #f37122;
    --orange-deep: #e8650f;
    --black: #000000;
    --grey: #5c5c5c;
    --stage: #e9e9e9;
    --poly-light: #fbfbfb;
    --poly-mid: #ececec;
  }
  * { box-sizing: border-box; margin: 0; padding: 0; }
  html, body {
    width: 1200px; height: 873px; overflow: hidden;
    background: var(--stage);
    font-family: "Lato", Arial, sans-serif;
  }
  .stage {
    width: 1200px; height: 873px;
    display: flex; align-items: center; justify-content: center; gap: 30px;
  }
  .card {
    position: relative; width: 560px; height: 320px; overflow: hidden;
    box-shadow: 0 6px 18px rgba(0,0,0,.18);
  }

  /* ---------- Brand lockup ---------- */
  .brand { display: flex; align-items: center; gap: 12px; }
  .brand__mark { width: 46px; height: 46px; border-radius: 50%; background: var(--orange); flex: none; }
  .brand__name { font-weight: 900; font-size: 17px; letter-spacing: 1px; text-transform: uppercase; color: var(--black); white-space: nowrap; }

  /* ---------- Back (white with orange service band) ---------- */
  .card--back { background: var(--white); color: var(--black); }
  .card--back .brand { position: absolute; top: 40px; left: 0; right: 0; justify-content: center; }
  .service-band {
    position: absolute; top: 118px; left: 0; right: 0; height: 118px;
    background: linear-gradient(135deg, var(--orange), var(--orange-deep));
    display: flex; align-items: center; justify-content: center;
  }
  .services {
    list-style: none; width: 480px;
    display: flex; flex-wrap: wrap; justify-content: center; gap: 10px 28px;
    color: var(--white); font-size: 13.5px; letter-spacing: .2px;
  }
  .services li { white-space: nowrap; }
  .services li::before { content: "•"; margin-right: 7px; }
  .tagline {
    position: absolute; bottom: 38px; left: 0; right: 0; text-align: center;
    color: var(--black); font-weight: 700; font-size: 14px;
  }
  .rule--back { position: absolute; bottom: 28px; left: 200px; right: 200px; height: 2px; background: var(--orange); }

  /* ---------- Front (white) ---------- */
  .card--front { background: var(--white); color: var(--black); }
  .poly-texture { position: absolute; inset: 0; }
  .card--front .brand { position: absolute; top: 34px; left: 150px; }
  .web-info { position: absolute; top: 96px; right: 52px; text-align: right; font-size: 13px; line-height: 1.45; }
  .web-info .label { color: var(--orange); }
  .rule { position: absolute; height: 2px; background: var(--orange); }
  .rule--top { top: 136px; left: 300px; right: 52px; }
  .rule--mid { top: 196px; left: 40px; width: 180px; }
  .person { position: absolute; top: 128px; left: 62px; }
  .person__name { color: var(--orange); font-weight: 700; font-size: 19px; }
  .person__role { font-size: 13px; margin-top: 1px; }
  .company {
    position: absolute; top: 186px; left: 228px;
    color: var(--orange); font-weight: 700; font-size: 16px; white-space: nowrap;
  }
  .contacts {
    position: absolute; top: 218px; left: 150px; list-style: none;
    display: grid; grid-template-columns: 150px 200px; gap: 8px 14px; font-size: 14px;
  }
  .contacts li { display: flex; align-items: center; gap: 8px; white-space: nowrap; }
  .contacts svg { width: 16px; height: 16px; fill: var(--orange); flex: none; }
  .address {
    position: absolute; bottom: 22px; left: 0; right: 0; text-align: center;
    color: var(--orange); font-weight: 700; font-size: 14px; white-space: nowrap;
  }
</style>
</head>
<body>
<main class="stage">

  <section class="card card--back" aria-label="Business card back">
    <div class="brand">
      <span class="brand__mark"></span>
      <span class="brand__name">Kestrel Asia Pacific Pte Ltd</span>
    </div>
    <div class="service-band">
      <ul class="services">
        <li>Remote Automation</li>
        <li>IP Video Surveillance</li>
        <li>Serial / Fieldbus Connectivity</li>
        <li>Industrial &amp; Embedded Computing</li>
        <li>Industrial Ethernet / Wireless / Cellular</li>
      </ul>
    </div>
    <p class="tagline">Industrial Networking and Computing Specialist</p>
    <div class="rule--back"></div>
  </section>

  <section class="card card--front" aria-label="Business card front">
    <div class="poly-texture" role="img" aria-label="Faint grey low-poly geometric background texture"
         style="background: linear-gradient(160deg, var(--poly-light) 0%, var(--poly-mid) 45%, var(--poly-light) 70%, var(--poly-mid) 100%);"></div>

    <div class="brand">
      <span class="brand__mark"></span>
      <span class="brand__name">Kestrel Asia Pacific Pte Ltd</span>
    </div>

    <div class="web-info">
      <div>www.kestrelap.com.sg</div>
      <div><span class="label">UEN No:</span> 200412345K</div>
    </div>
    <div class="rule rule--top"></div>

    <div class="person">
      <div class="person__name">Daniel Koh</div>
      <div class="person__role">Sales Manager</div>
    </div>

    <div class="rule rule--mid"></div>
    <div class="company">Kestrel Asia Pacific Pte Ltd</div>

    <ul class="contacts">
      <li>
        <svg viewBox="0 0 24 24" aria-hidden="true"><path d="M6.6 10.8a15 15 0 0 0 6.6 6.6l2.2-2.2a1 1 0 0 1 1-.25 11.4 11.4 0 0 0 3.6.57 1 1 0 0 1 1 1V20a1 1 0 0 1-1 1A17 17 0 0 1 3 4a1 1 0 0 1 1-1h3.5a1 1 0 0 1 1 1c0 1.25.2 2.45.57 3.57a1 1 0 0 1-.25 1z"/></svg>
        +65 6123 4501
      </li>
      <li>
        <svg viewBox="0 0 24 24" aria-hidden="true"><path d="M6 3h12v5H6zM4 9h16a2 2 0 0 1 2 2v6h-4v4H6v-4H2v-6a2 2 0 0 1 2-2zm4 7v3h8v-3z"/></svg>
        +65 9123 4567
      </li>
      <li>
        <svg viewBox="0 0 24 24" aria-hidden="true"><path d="M3 5h18v14H3zm2 2v.5l7 4.5 7-4.5V7zm0 2.9V17h14V9.9l-7 4.5z"/></svg>
        +65 6123 4502
      </li>
      <li>
        <svg viewBox="0 0 24 24" aria-hidden="true"><path d="M7 2h10a2 2 0 0 1 2 2v16a2 2 0 0 1-2 2H7a2 2 0 0 1-2-2V4a2 2 0 0 1 2-2zm0 3v13h10V5zm5 14.2a1 1 0 1 0 0 .01z"/></svg>
        sales@kestrelap.com.sg
      </li>
    </ul>

    <p class="address">21 Kallang Way Tech Hub #02-15 (Lobby B), Singapore, 349250</p>
  </section>

</main>
</body>
</html>
```